Landscape design build company door flyer

I would like this flyer to convey a high-level of professionalism for a company that is excellent with communication with their clients as well as a company that does incredible installations

Went on vacation/holiday

```html
<!DOCTYPE html>
<html lang="en">
<head>
<meta charset="utf-8">
<title>Summit Stone Builders – Outdoor Living Spaces Flyer</title>
<link href="https://fonts.googleapis.com/css2?family=Roboto:wght@900&family=Roboto+Condensed:wght@400;700&family=Marcellus&family=Montserrat:wght@600&family=Fira+Sans:wght@500&display=swap" rel="stylesheet">
<style>
  :root{
    --navy:#0d2a40;
    --navy-soft:#1f3d55;
    --paper:#ffffff;
    --mist:#e6e7e8;
    --backdrop:#e4e4e4;
    --muted:#c9cfd5;
    --ink:#1b2631;
  }
  html,body{margin:0;padding:0;width:1200px;height:1029px;overflow:hidden;background:var(--backdrop);}
  .flyer{position:absolute;left:244px;top:57px;width:711px;height:914px;background:var(--paper);overflow:hidden;box-shadow:0 6px 22px rgba(0,0,0,.18);}
  .art{position:absolute;left:0;top:0;width:711px;height:914px;}
  .headline{position:absolute;left:100px;top:18px;width:511px;margin:0;text-align:center;color:var(--paper);font:900 31px/40px "Roboto",sans-serif;letter-spacing:.5px;}
  .brand{position:absolute;left:0;width:711px;text-align:center;color:var(--navy);}
  .brand-name{top:382px;margin:0;font:400 36px/40px "Marcellus",serif;letter-spacing:.5px;}
  .brand-tag{top:420px;margin:0;font:600 17px/20px "Montserrat",sans-serif;letter-spacing:-.3px;}
  .intro{position:absolute;left:40px;top:470px;width:330px;margin:0;color:var(--ink);font:400 16px/20px "Roboto Condensed",sans-serif;}
  .services{position:absolute;left:40px;top:560px;width:340px;margin:0;padding:0;list-style:none;display:grid;grid-template-columns:167px 173px;row-gap:14px;}
  .services li{display:flex;align-items:center;height:24px;color:var(--ink);font:500 13.5px/16px "Fira Sans",sans-serif;}
  .services svg{width:26px;height:26px;margin-right:8px;flex:none;}
  .areas{position:absolute;left:40px;top:752px;width:340px;margin:0;color:var(--paper);font:400 14px/17px "Roboto Condensed",sans-serif;}
  .cta{position:absolute;left:40px;top:795px;margin:0;color:var(--muted);font:700 26px/30px "Roboto Condensed",sans-serif;}
  .phone{position:absolute;left:42px;top:832px;display:flex;align-items:center;color:var(--paper);font:900 43px/48px "Roboto",sans-serif;}
  .phone svg{width:44px;height:44px;margin-right:13px;}
  .contact{position:absolute;left:462px;display:flex;align-items:center;font:700 17px/20px "Roboto Condensed",sans-serif;}
  .contact svg{width:22px;height:22px;margin-right:10px;}
  .contact-email{top:814px;color:var(--paper);}
  .contact-web{top:872px;color:var(--navy);}
</style>
</head>
<body>
<main class="flyer">
  <svg class="art" viewBox="0 0 711 914" xmlns="http://www.w3.org/2000/svg">
    <defs>
      <linearGradient id="patioTone" x1="0" y1="0" x2="1" y2="1">
        <stop offset="0" stop-color="#5d7a48"/>
        <stop offset=".45" stop-color="#5a5f66"/>
        <stop offset="1" stop-color="#3f5166"/>
      </linearGradient>
      <linearGradient id="driveTone" x1="0" y1="0" x2="0" y2="1">
        <stop offset="0" stop-color="#6c7480"/>
        <stop offset="1" stop-color="#4c4a46"/>
      </linearGradient>
      <linearGradient id="lakeTone" x1="0" y1="0" x2="0" y2="1">
        <stop offset="0" stop-color="#6f8db3"/>
        <stop offset=".55" stop-color="#2c3a52"/>
        <stop offset="1" stop-color="#5a4a40"/>
      </linearGradient>
    </defs>

    <rect class="hero-photo" x="0" y="0" width="711" height="360" fill="url(#patioTone)" role="img" aria-label="Photo of a stone outdoor kitchen and covered patio with timber posts"/>
    <line x1="355" y1="112" x2="355" y2="290" stroke="#ffffff" stroke-width="8"/>
    <polygon points="94,0 617,0 549,116 164,116" fill="#ffffff"/>
    <polygon points="100,0 611,0 546,112 167,112" fill="var(--navy)"/>

    <rect x="0" y="790" width="711" height="124" fill="var(--mist)"/>
    <polygon points="0,741 372,741 441,790 711,790 711,859 441,859 401,899 0,899" fill="var(--navy)"/>

    <polygon points="583,419 751,516 751,710 583,807 415,710 415,516" fill="var(--mist)"/>
    <polygon points="583,442 731,528 731,698 583,784 435,698 435,528" fill="var(--navy)"/>
    <polygon points="583,463 713,538 713,688 583,763 453,688 453,538" fill="#ffffff"/>
    <polygon points="583,477 701,545 701,681 583,749 465,681 465,545" fill="url(#driveTone)" role="img" aria-label="Aerial photo of a home with a new paver driveway and planted beds"/>

    <polygon points="476,624 552,668 552,756 476,800 400,756 400,668" fill="var(--mist)"/>
    <polygon points="476,632 545,672 545,752 476,792 407,752 407,672" fill="#ffffff"/>
    <polygon points="476,638 540,675 540,749 476,786 412,749 412,675" fill="var(--navy)"/>
    <polygon points="476,646 533,679 533,745 476,778 419,745 419,679" fill="#ffffff"/>
    <polygon points="476,652 528,682 528,742 476,772 424,742 424,682" fill="url(#lakeTone)" role="img" aria-label="Photo of a lakeside patio with a lit fire pit and lounge chairs at dusk"/>
  </svg>

  <h1 class="headline">DO YOU NEED A TRUSTED<br>BUILDING CONTRATOR?</h1>

  <p class="brand brand-name">SUMMIT STONE BUILDERS</p>
  <p class="brand brand-tag">OUTDOOR LIVING SPACES</p>

  <p class="intro">At Summit Stone Builders, our passion is to go above and beyond to craft amazing outdoor environments for clients. Our services are:</p>

  <ul class="services">
    <li><svg viewBox="0 0 26 26"><path d="M2 25V9L13 2l11 7v16" fill="none" stroke="var(--navy)" stroke-width="2"/><rect x="8" y="12" width="10" height="9" fill="none" stroke="var(--navy)" stroke-width="1.6"/></svg>Paver Patios</li>
    <li><svg viewBox="0 0 26 26"><path d="M2 25V9L13 2l11 7v16" fill="none" stroke="var(--navy)" stroke-width="2"/><path d="M7 20h12M7 16h12M8 13h10v8" fill="none" stroke="var(--navy)" stroke-width="1.6"/></svg>Decks &amp; Railings</li>
    <li><svg viewBox="0 0 26 26"><path d="M2 25V9L13 2l11 7v16" fill="none" stroke="var(--navy)" stroke-width="2"/><path d="M6 20l4-6h6l4 6z" fill="var(--navy)"/></svg>Paver Driveways</li>
    <li><svg viewBox="0 0 26 26"><path d="M2 25V9L13 2l11 7v16" fill="none" stroke="var(--navy)" stroke-width="2"/><path d="M8 21v-6l5-4 5 4v6z" fill="none" stroke="var(--navy)" stroke-width="1.6"/></svg>Firepits &amp; Fireplaces</li>
    <li><svg viewBox="0 0 26 26"><path d="M2 25V9L13 2l11 7v16" fill="none" stroke="var(--navy)" stroke-width="2"/><path d="M7 12h10v3H7zM9 16h10v3H9z" fill="var(--navy)"/></svg>Retaining Walls</li>
    <li><svg viewBox="0 0 26 26"><path d="M2 25V9L13 2l11 7v16" fill="none" stroke="var(--navy)" stroke-width="2"/><path d="M13 10v3M10 13h6l-1 6h-4z" fill="none" stroke="var(--navy)" stroke-width="1.6"/></svg>Outdoor Lighting</li>
    <li><svg viewBox="0 0 26 26"><path d="M2 25V9L13 2l11 7v16" fill="none" stroke="var(--navy)" stroke-width="2"/><path d="M6 18c2-2 4 2 7 0s5 2 7 0M6 21c2-2 4 2 7 0s5 2 7 0M10 16v-6M16 16v-6" fill="none" stroke="var(--navy)" stroke-width="1.5"/></svg>Pools</li>
    <li><svg viewBox="0 0 26 26"><path d="M2 25V9L13 2l11 7v16" fill="none" stroke="var(--navy)" stroke-width="2"/><circle cx="13" cy="16" r="5" fill="none" stroke="var(--navy)" stroke-width="1.4"/><path d="M13 13v6M10 16h6" stroke="var(--navy)" stroke-width="1.4"/></svg>And More...</li>
  </ul>

  <p class="areas">Our service areas includes Bellevue, Issaquah, Kirkland, Redmond, Sammamish.</p>
  <p class="cta">CONTACT US TODAY</p>
  <div class="phone">
    <svg viewBox="0 0 44 44"><path d="M6 8c3-3 6-3 8 0l4 5c1 2 0 4-2 5l-2 2c2 5 6 9 11 11l2-2c1-2 3-3 5-2l5 4c3 2 3 5 0 8-4 4-12 3-20-5S2 12 6 8z" fill="#ffffff"/><path d="M25 6a13 13 0 0 1 13 13M25 12a7 7 0 0 1 7 7" fill="none" stroke="#ffffff" stroke-width="3"/></svg>
    [206]-555-014
  </div>

  <div class="contact contact-email">
    <svg viewBox="0 0 22 22"><rect x="1" y="4" width="20" height="14" fill="#ffffff"/><path d="M1 4l10 8 10-8" fill="none" stroke="var(--navy)" stroke-width="2"/></svg>
    info@summitstonebuilders.com
  </div>
  <div class="contact contact-web">
    <svg viewBox="0 0 22 22"><circle cx="11" cy="11" r="9" fill="none" stroke="var(--navy)" stroke-width="1.6"/><ellipse cx="11" cy="11" rx="4" ry="9" fill="none" stroke="var(--navy)" stroke-width="1.4"/><path d="M2 11h18M4 6h14M4 16h14" stroke="var(--navy)" stroke-width="1.4"/></svg>
    www.summitstonebuilders.com
  </div>
</main>
</body>
</html>
```